Mental Health Clinic Website

website for a mental health clinic. two files describing the website are attached, in case of conflicting info the word document is priority.

Target Market(s)

Ohio / Pennsylvania residents

Industry/Entity Type

Health Care

Coding

Coded - Design and coding required

Number of Pages Required

5+ page

Requirements
Must have
• see attached

```html
<!DOCTYPE html>
<html lang="en">
<head>
<meta charset="utf-8">
<title>Dr Halloran Serenity Center</title>
<link rel="stylesheet" href="https://fonts.googleapis.com/css2?family=Lato:ital,wght@0,400;0,700;0,900;1,400&display=swap">
<style>
:root{
  --green:#6fb83a;
  --green-dark:#4f9a2c;
  --blue:#1b4fae;
  --blue-link:#2a6dd0;
  --ink:#1c1c1c;
  --text:#555;
  --muted:#888;
  --grey-bg:#f1f1f1;
  --white:#fff;
  --line:#dcdcdc;
}
*{box-sizing:border-box;margin:0;padding:0}
html,body{width:1200px;height:5143px;overflow:hidden}
body{font-family:'Lato',sans-serif;color:var(--text);background:var(--white);position:relative}
a{color:inherit;text-decoration:none}

/* hero */
.hero{position:absolute;top:0;left:0;width:1200px;height:662px;
  background:linear-gradient(180deg,#34424c 0%,#5a4a5c 30%,#c4506a 55%,#e07a6a 68%,#3b2f35 85%,#1e1e22 100%)}
.topbar{position:absolute;top:0;left:0;right:0;height:34px;background:rgba(0,0,0,.35);
  display:flex;justify-content:space-between;align-items:center;padding:0 113px;font-size:12px;color:var(--white)}
.topbar span{display:flex;align-items:center;gap:6px}
.topbar .right{display:flex;gap:18px}
.topbar svg{fill:var(--green)}
.brand{position:absolute;top:60px;left:100px;display:flex;flex-direction:column;align-items:center;gap:10px}
.brand .mark{width:90px;height:90px;border-radius:50%;background:var(--white)}
.brand .name{font-size:12px;color:var(--white);font-weight:400}
.nav{position:absolute;top:92px;right:100px;display:flex;gap:24px;font-size:14px;font-weight:700;color:var(--white);align-items:center}
.nav .active{color:var(--green)}
.hero h1{position:absolute;top:250px;left:0;width:100%;text-align:center;color:var(--white);font-weight:700;line-height:1.2}
.hero h1 .l1{display:block;font-size:56px}
.hero h1 .l2{display:block;font-size:68px}
.dots{position:absolute;top:576px;left:0;width:100%;display:flex;justify-content:center;gap:6px}
.dots i{width:12px;height:12px;border-radius:50%;border:2px solid var(--white)}
.dots i.on{background:var(--white)}

/* intro */
.intro{position:absolute;top:735px;left:223px;width:754px;text-align:center;font-size:13px;line-height:26px;color:var(--text)}
.intro p+p{margin-top:24px}

/* about */
.about{position:absolute;top:1183px;left:0;width:1200px;height:497px;background:var(--grey-bg)}
.about .copy{position:absolute;top:80px;left:113px;width:490px}
.about h2{font-size:46px;font-weight:900;color:var(--ink);margin-bottom:32px}
.about p{font-size:13px;line-height:25px}
.about .note{font-style:italic;margin:14px 0 22px}
.about h3{font-size:16px;font-weight:700;color:var(--ink);margin-bottom:20px}
.langs{display:flex;gap:26px;font-size:13px;color:var(--ink)}
.langs span{display:flex;align-items:center;gap:8px}
.langs i{width:32px;height:32px;border-radius:50%}
.about .photo{position:absolute;top:88px;left:648px;width:442px;height:358px;
  background:linear-gradient(180deg,#e9a24a 0%,#d67a34 35%,#5a4a45 70%,#2e2a2c 100%)}

/* team */
.team{position:absolute;top:1680px;left:0;width:1200px;height:653px;text-align:center}
.section-title{font-size:42px;font-weight:700;color:var(--ink)}
.team .section-title{margin-top:48px}
.team-grid{position:absolute;top:138px;left:103px;width:994px;display:flex;justify-content:space-between}
.member{width:190px}
.member .avatar{width:188px;height:188px;border-radius:50%;border:3px solid #e5e5e5;margin:0 auto 14px;
  background:linear-gradient(180deg,#eef1f4 0%,#d3dbe2 100%)}
.member h4{font-size:17px;font-weight:700;color:var(--ink)}
.member .role{font-size:12px;font-style:italic;color:var(--muted);margin:6px 0 14px}
.member p{font-size:12px;line-height:19px}
.member a{display:block;margin-top:16px;font-size:12px;font-weight:700;color:var(--green-dark);text-decoration:underline}

/* services */
.services{position:absolute;top:2333px;left:0;width:1200px;height:919px;background:var(--blue);color:var(--white)}
.services .section-title{color:var(--white);text-align:center;margin-top:70px}
.svc-grid{position:absolute;top:170px;left:103px;width:994px;display:flex;justify-content:space-between;text-align:center}
.svc{width:190px}
.svc .ring{width:166px;height:166px;border-radius:50%;background:var(--white);margin:0 auto 22px;
  display:flex;align-items:center;justify-content:center;box-shadow:0 6px 0 rgba(0,0,0,.15)}
.svc .ring.first{box-shadow:0 8px 0 var(--green)}
.svc .icon{width:90px;height:90px;border-radius:50%;background:radial-gradient(circle,#8fd05a 0%,#5fae30 100%)}
.svc h4{font-size:20px;font-weight:700;line-height:24px}
.svc-detail{position:absolute;top:507px;left:113px;width:974px;display:flex;gap:52px}
.svc-detail .photo{width:474px;height:309px;flex:none;
  background:linear-gradient(135deg,#a9c4dc 0%,#e8eef4 45%,#c9d6e2 70%,#7e98b4 100%)}
.svc-detail .text{padding-top:14px;font-size:13px;line-height:24px}
.svc-detail .text p+p{margin-top:18px}

/* good reads */
.reads{position:absolute;top:3252px;left:0;width:1200px;height:898px;text-align:center}
.reads .section-title{margin-top:105px}
.book{position:absolute;top:229px;width:463px;height:608px;border:1px solid var(--line);padding:50px 50px 0}
.book .cover{width:180px;height:272px;margin:0 auto 48px;
  background:linear-gradient(180deg,#fafafa 0%,#e9e9e9 100%);box-shadow:6px 6px 14px rgba(0,0,0,.18)}
.book h4{font-size:22px;font-weight:700;color:var(--ink)}
.book .author{font-size:17px;color:var(--blue-link);margin:12px 0 20px}
.book p{font-size:12px;line-height:21px}

/* contact */
.contact{position:absolute;top:4150px;left:0;width:1200px;height:686px;text-align:center}
.contact .section-title{margin-top:85px}
.map{position:absolute;top:199px;left:113px;width:597px;height:446px;
  background:linear-gradient(135deg,#e6e2d8 0%,#d9e6cc 40%,#ece8de 70%,#cfe0c0 100%)}
.map .pin{position:absolute;top:200px;left:310px}
.form{position:absolute;top:199px;left:710px;width:377px;height:446px;background:var(--green);padding:36px 40px;text-align:left}
.form h3{font-size:22px;font-weight:400;color:var(--white);margin-bottom:28px}
.form .field{height:36px;background:var(--white);margin-bottom:16px;padding-left:12px;line-height:36px;font-size:12px;color:var(--muted)}
.form .check{font-size:15px;font-weight:700;color:var(--white);margin:8px 0 30px}
.form .submit{display:inline-block;background:var(--blue);color:var(--white);font-size:12px;font-weight:700;padding:8px 26px;border-radius:20px}

/* footer */
.footer{position:absolute;top:4836px;left:0;width:1200px;height:307px}
.footer .brand-foot{position:absolute;top:40px;left:100px;display:flex;flex-direction:column;align-items:center;gap:10px}
.footer .brand-foot .mark{width:100px;height:100px;border-radius:50%;background:#e7f1dc}
.footer .brand-foot .name{font-size:12px;color:var(--ink)}
.socials{position:absolute;top:67px;left:362px;display:flex;gap:12px}
.socials i{width:44px;height:44px;border-radius:50%;border:2px solid var(--green)}
.foot-contact{position:absolute;top:152px;left:362px;display:flex;gap:14px;font-size:12px;color:var(--text);align-items:center}
.foot-contact span{display:flex;align-items:center;gap:6px}
.foot-contact svg{fill:var(--green)}
.foot-links{position:absolute;top:196px;left:356px;display:flex;font-size:12px}
.foot-links a{padding:0 14px;border-right:1px solid var(--muted)}
.foot-links a:last-child{border:none}
.copyright{position:absolute;top:238px;left:362px;font-size:12px}
</style>
</head>
<body>

<header class="hero">
  <div class="topbar">
    <span><svg width="10" height="13" viewBox="0 0 10 13"><path d="M5 0a5 5 0 0 0-5 5c0 4 5 8 5 8s5-4 5-8a5 5 0 0 0-5-5zm0 7a2 2 0 1 1 0-4 2 2 0 0 1 0 4z"/></svg>2480 Birchwood Lane, Suite 210, Maple Falls, OH 44000</span>
    <div class="right">
      <span><svg width="12" height="12" viewBox="0 0 12 12"><path d="M2.5 0 4.5 3 3 4.5c.8 1.8 2.7 3.7 4.5 4.5L9 7.5l3 2L10.5 12C5 12 0 7 0 1.5z"/></svg>(440) 555-0182</span>
      <span><svg width="13" height="10" viewBox="0 0 13 10"><path d="M0 0h13v10H0zm1 1 5.5 4L12 1z" fill-rule="evenodd"/></svg>info@halloranclinic.com</span>
    </div>
  </div>
  <div class="brand"><div class="mark"></div><div class="name">Dr Halloran Serenity Center</div></div>
  <nav class="nav">
    <a class="active">HOME</a><a>ABOUT US</a><a>SERVICES</a><a>GOOD READS</a><a>CONTACT</a>
    <svg width="14" height="14" viewBox="0 0 14 14"><circle cx="6" cy="6" r="4.5" fill="none" stroke="#fff" stroke-width="2"/><path d="M9.5 9.5 13 13" stroke="#fff" stroke-width="2"/></svg>
  </nav>
  <h1><span class="l1">Dr Halloran</span><span class="l2">Serenity Center</span></h1>
  <div class="dots"><i class="on"></i><i></i><i></i><i></i></div>
</header>

<section class="intro">
  <p>Each individual is unique with unique personality and unique needs. Therefore we provide individual treatment customized for you or your child. Multiculturalism also informs our practice. We are a full service mental health practice with the capacity to serve adults, children, teens and their parents.</p>
  <p>We provide high quality evidence based treatment and care including medication management, pharmacogenomic testing, individual psychotherapy, group psychotherapy, art therapy, CBT, DBT and trauma therapy. Our providers are experts in treating variety of illnesses such as depression, anxiety, schizophrenia, ADHD, gender identity concerns and PTSD.</p>
  <p>We are experienced in a variety of methods that help people achieve their psychological goals, and we will discuss with you the best ways to attain the health and wellness that you deserve. We are committed to helping you achieve your optimal level of emotional functioning and fulfill a successful life.</p>
</section>

<section class="about">
  <div class="copy">
    <h2>ABOUT US</h2>
    <p>You will find a number of highly specialized – experienced and caring therapists and psychiatrists in Serenity Center. We provide medication management and psychotherapy (counseling) across the lifespan.</p>
    <p class="note">– children, teens and adults.</p>
    <h3>Other than English, we speak the following languages</h3>
    <div class="langs">
      <span><i style="background:#d9342b"></i>Spanish</span>
      <span><i style="background:#2a2a2a"></i>German</span>
      <span><i style="background:#3c9a4a"></i>Farsi</span>
      <span><i style="background:#2f5ec4"></i>Hebrew</span>
    </div>
  </div>
  <div class="photo" role="img" aria-label="Person doing yoga on a beach at sunset"></div>
</section>

<section class="team">
  <h2 class="section-title">MEET OUR TEAM</h2>
  <div class="team-grid">
    <div class="member"><div class="avatar" role="img" aria-label="Portrait of a team doctor"></div><h4>Finibus Bonorum</h4><div class="role">Nam libero tem</div><p>Temporibus autem qui busdam et aut officiis debit is aut rerum necessitatibus saepe evenie ut</p><a>MAKE AN APPOINTMENT</a></div>
    <div class="member"><div class="avatar" role="img" aria-label="Portrait of a team doctor"></div><h4>Finibus Bonorum</h4><div class="role">Nam libero tem</div><p>Temporibus autem qui busdam et aut officiis debit is aut rerum necessitatibus saepe evenie ut</p><a>MAKE AN APPOINTMENT</a></div>
    <div class="member"><div class="avatar" role="img" aria-label="Portrait of a team doctor"></div><h4>Finibus Bonorum</h4><div class="role">Nam libero tem</div><p>Temporibus autem qui busdam et aut officiis debit is aut rerum necessitatibus saepe evenie ut</p><a>MAKE AN APPOINTMENT</a></div>
    <div class="member"><div class="avatar" role="img" aria-label="Portrait of a team doctor"></div><h4>Finibus Bonorum</h4><div class="role">Nam libero tem</div><p>Temporibus autem qui busdam et aut officiis debit is aut rerum necessitatibus saepe evenie ut</p><a>MAKE AN APPOINTMENT</a></div>
    <div class="member"><div class="avatar" role="img" aria-label="Portrait of a team doctor"></div><h4>Finibus Bonorum</h4><div class="role">Nam libero tem</div><p>Temporibus autem qui busdam et aut officiis debit is aut rerum necessitatibus saepe evenie ut</p><a>MAKE AN APPOINTMENT</a></div>
  </div>
</section>

<section class="services">
  <h2 class="section-title">SERVICES</h2>
  <div class="svc-grid">
    <div class="svc"><div class="ring first"><div class="icon" role="img" aria-label="Medication management icon"></div></div><h4>Medication<br>management</h4></div>
    <div class="svc"><div class="ring"><div class="icon" role="img" aria-label="Psychotherapy icon"></div></div><h4>Psychotherapy</h4></div>
    <div class="svc"><div class="ring"><div class="icon" role="img" aria-label="Treatment approach icon"></div></div><h4>Treatment<br>Approach</h4></div>
    <div class="svc"><div class="ring"><div class="icon" role="img" aria-label="Art therapy icon"></div></div><h4>Art Therapy</h4></div>
    <div class="svc"><div class="ring"><div class="icon" role="img" aria-label="Treatment areas icon"></div></div><h4>Treatment<br>Areas</h4></div>
  </div>
  <div class="svc-detail">
    <div class="photo" role="img" aria-label="Doctor writing notes at a desk with medication bottles"></div>
    <div class="text">
      <p>Nemo enim ipsam voluptatem quia voluptas sit aspernatur autit aut fugit, sed quia consequuntur magni eum iure reprehender qui in ea voluptate velit esse quam nihil.</p>
      <p>Dolores eos qui ratione voluptatem sequi nesciunt. Neque porro quisquam est, qui dolorem ipsum quia dolor sit amet, consectetur adipisci velit, sed quia non numquam eius modi tempora incidunt ut labore et dolore magnam aliquam quaerat voluptatem. Ut enim ad minima veniam, quis nostrum exerci.</p>
    </div>
  </div>
</section>

<section class="reads">
  <h2 class="section-title">GOOD READS</h2>
  <article class="book" style="left:113px">
    <div class="cover" role="img" aria-label="Book cover with a colourful tree"></div>
    <h4>Finibus Bonoruet Malor</h4>
    <div class="author">Mara Quinn</div>
    <p>Nemo enim ipsam voluptatem quia voluptas sit aspur aut odit aut fugit, sed quia consequuntur magni dolores eos qui ratione voluptatem sequi nesciu que porro quis quam est, qui dol orem ipsum quia dolletur.</p>
  </article>
  <article class="book" style="left:628px">
    <div class="cover" role="img" aria-label="Book cover with a figure holding up a tree"></div>
    <h4>Finibus Bonoruet Malor</h4>
    <div class="author">Daniel</div>
    <p>Nemo enim ipsam voluptatem quia voluptas sit aspur aut odit aut fugit, sed quia consequuntur magni dolores eos qui ratione voluptatem sequi nesciu que porro quis quam est, qui dol orem ipsum quia dolletur.</p>
  </article>
</section>

<section class="contact">
  <h2 class="section-title">CONTACT US</h2>
  <div class="map" role="img" aria-label="Street map showing the clinic location">
    <svg class="pin" width="26" height="36" viewBox="0 0 26 36"><path d="M13 0A13 13 0 0 0 0 13c0 10 13 23 13 23s13-13 13-23A13 13 0 0 0 13 0z" fill="#d8342b"/><circle cx="13" cy="13" r="5" fill="#8e1a14"/></svg>
  </div>
  <div class="form">
    <h3>Appointment Request</h3>
    <div class="field">First Name</div>
    <div class="field">Last Name</div>
    <div class="field">Email</div>
    <div class="field">Tel</div>
    <div class="check">Please contact me for an appointment</div>
    <span class="submit">SUBMIT</span>
  </div>
</section>

<footer class="footer">
  <div class="brand-foot"><div class="mark"></div><div class="name">Dr Halloran Serenity Center</div></div>
  <div class="socials"><i></i><i></i><i></i><i></i></div>
  <div class="foot-contact">
    <span><svg width="10" height="13" viewBox="0 0 10 13"><path d="M5 0a5 5 0 0 0-5 5c0 4 5 8 5 8s5-4 5-8a5 5 0 0 0-5-5zm0 7a2 2 0 1 1 0-4 2 2 0 0 1 0 4z"/></svg>2480 Birchwood Lane, Suite 210, Maple Falls, OH 44000</span>
    <span>|</span>
    <span><svg width="12" height="12" viewBox="0 0 12 12"><path d="M2.5 0 4.5 3 3 4.5c.8 1.8 2.7 3.7 4.5 4.5L9 7.5l3 2L10.5 12C5 12 0 7 0 1.5z"/></svg>(440) 555-0182</span>
    <span>|</span>
    <span><svg width="13" height="10" viewBox="0 0 13 10"><path d="M0 0h13v10H0zm1 1 5.5 4L12 1z" fill-rule="evenodd"/></svg>info@halloranclinic.com</span>
  </div>
  <nav class="foot-links"><a>Help</a><a>FAQ</a><a>Support</a><a>Sitemap</a><a>Terms Of Use</a><a>Privacy Statement</a></nav>
  <div class="copyright">Dr Halloran Serenity Center © 2019 All rights reserved</div>
</footer>

</body>
</html>
```